Plumo Ridge - Graphic Label

Company Name: Verdant Loom
Product: Organic Energy Drink
Name of Drink : Plumo Ridge
8.45oz - Bottle
http://www.trellimart.example/item/metal-beverage-flask_2749301856.html?s=p
Attached will be examples of labels for other drinks associated with this company along with company logo. I'm open to all interpretations of design. Please submit creative ideas and we can adjust design as we go.
Design must have some integration of the geometry as seen in labels attached.
Keep it classy
If you have a vision for the design, just create it and we can adjust from there.
I want the bottle to have long lasting but creative/interesting design..
Reason: Design sought has not been submited, the deadline has been extended.
Please continue submissions.
- Thanks
Target Market(s)
All Ages .. those interested in Organics, health drinks, energy drinks
Industry/Entity Type
It Company
Look and feel

```html
<!DOCTYPE html>
<html lang="en">
<head>
<meta charset="utf-8">
<title>Plumo Ridge – Organic Energy Label</title>
<link rel="stylesheet" href="https://fonts.googleapis.com/css2?family=Fredoka:wght@600&family=Montserrat:wght@700;800&family=Pacifico&display=swap">
<style>
  :root {
    --purple-deep: #3f1476;
    --purple: #4f1d92;
    --purple-light: #7a3fc4;
    --gold-dark: #6e5223;
    --gold: #b08a45;
    --gold-light: #d6b878;
    --white: #ffffff;
    --page: #f4f2f6;
  }
  html, body {
    margin: 0;
    padding: 0;
    width: 1012px;
    height: 1200px;
    overflow: hidden;
    background: var(--page);
  }
  .label {
    display: block;
    width: 1012px;
    height: 1200px;
  }
  .band { fill: var(--purple); }
  .band-deep { fill: var(--purple-deep); }
  .panel-outline { fill: none; stroke: var(--purple-light); stroke-width: 4; }
  .maker-name {
    font-family: "Montserrat", sans-serif;
    font-weight: 700;
    font-size: 34px;
    letter-spacing: 2px;
    fill: var(--white);
  }
  .maker-dot { fill: var(--gold-light); }
  .product-name {
    font-family: "Fredoka", sans-serif;
    font-weight: 600;
    font-size: 160px;
    fill: var(--white);
  }
  .product-sub {
    font-family: "Montserrat", sans-serif;
    font-weight: 800;
    font-size: 64px;
    letter-spacing: 8px;
    fill: var(--white);
  }
  .claim {
    font-family: "Montserrat", sans-serif;
    font-weight: 800;
    font-size: 26px;
    fill: var(--white);
  }
  .tagline {
    font-family: "Pacifico", cursive;
    font-size: 66px;
    fill: var(--purple);
  }
  .cert-badge { fill: var(--white); stroke: var(--purple-light); stroke-width: 4; }
</style>
</head>
<body>
<svg class="label" viewBox="0 0 1012 1200" xmlns="http://www.w3.org/2000/svg">
  <defs>
    <linearGradient id="goldSheen" x1="0" y1="0" x2="1" y2="0">
      <stop offset="0" stop-color="#5e451b"/>
      <stop offset="0.22" stop-color="#a07d3c"/>
      <stop offset="0.5" stop-color="#d2b271"/>
      <stop offset="0.78" stop-color="#a07d3c"/>
      <stop offset="1" stop-color="#5e451b"/>
    </linearGradient>
    <radialGradient id="berryTones" cx="0.5" cy="0.5" r="0.5">
      <stop offset="0" stop-color="#3a2340"/>
      <stop offset="0.65" stop-color="#1d0f24"/>
      <stop offset="1" stop-color="#4c7a2e" stop-opacity="0.8"/>
    </radialGradient>
  </defs>

  <!-- label body -->
  <rect class="body" x="0" y="0" width="1012" height="1200" fill="url(#goldSheen)"/>

  <!-- top band with chevron -->
  <polygon class="band" points="0,0 1012,0 1012,180 506,280 0,180"/>
  <circle class="maker-dot" cx="362" cy="118" r="12"/>
  <text class="maker-name" x="386" y="130">Verdant Loom</text>

  <!-- central name panel -->
  <polygon class="band" points="140,480 872,330 872,700 140,850"/>
  <polygon class="band-deep" points="690,368 872,330 872,500"/>
  <polygon class="panel-outline" points="690,368 872,330 872,500"/>
  <polygon class="band-deep" points="140,690 140,850 320,813"/>
  <polygon class="panel-outline" points="140,690 140,850 320,813"/>
  <polygon class="panel-outline" points="140,480 872,330 872,700 140,850"/>

  <text class="claim" x="790" y="398">No</text>
  <text class="claim" x="790" y="430">GMO</text>
  <text class="claim" x="158" y="748">100%</text>
  <text class="claim" x="158" y="780">Juice</text>

  <text class="product-name" x="506" y="620" text-anchor="middle">plumo</text>
  <text class="product-sub" x="506" y="700" text-anchor="middle">RIDGE</text>

  <!-- fruit illustration area -->
  <ellipse role="img" aria-label="Cluster of dark purple berries with green leaves" cx="506" cy="925" rx="130" ry="56" fill="url(#berryTones)"/>

  <text class="tagline" x="506" y="1045" text-anchor="middle">Organic Energy</text>

  <!-- bottom band with chevron -->
  <polygon class="band" points="0,1200 0,1110 506,1070 1012,1110 1012,1200"/>
  <circle class="cert-badge" cx="506" cy="1140" r="36"/>
</svg>
</body>
</html>
```